NEW Modern Sleek Business Card for VR Language Startup

Our startup is using VR to lead the next wave of world language education. We need a two-sided business card that introduces the larger organization (Brightloom Language Inc) and our contact info on one side and shows the product, Glimwoorld, on the other side.

Side 1 (contact info)= Brightloom Logo and Contact info (name, title, phone, email)

Side 2 (product)= Glimworld logo, text, and website
Text= Culturally Immersive Language Learning Games
Website= www.glimworld-play.com

Target Market(s)

Education, Technology

Contact Information for Business Card

Contact info will be updated upon approval of the design. For now, put this as a placeholder.

Perry Dunmore
Founder & CEO
pdunmore@quillpost-mail.net
(555)-014-2286

Font styles to use
Other font styles liked:
• Gibson and Century Gothic are the brand fonts

Requirements
Nice to have
• I would love to see cohesion between the design and colors of the two logos. I have attached a few business card designs that I like, so you can get a feel for my preferred style.

```html
<!DOCTYPE html>
<html lang="en">
<head>
<meta charset="utf-8">
<title>Brightloom Language – Business Card</title>
<link rel="stylesheet" href="https://fonts.googleapis.com/css2?family=Montserrat:wght@400;500;600&family=Questrial&display=swap">
<style>
  :root {
    --bg: #2b2824;
    --orange: #f9a11b;
    --red: #ee2a50;
    --magenta: #a12f97;
    --violet: #7a5cc0;
    --cyan: #43cbdc;
    --brand-blue: #4a63d8;
    --ink: #3a3a3a;
    --ink-soft: #555;
    --white: #ffffff;
    --card-radius: 22px;
  }
  * { box-sizing: border-box; margin: 0; padding: 0; }
  html, body { width: 1200px; height: 900px; overflow: hidden; }
  body {
    background: var(--bg);
    font-family: "Questrial", "Century Gothic", sans-serif;
    position: relative;
  }
  .card {
    position: absolute;
    width: 600px;
    height: 343px;
    border-radius: var(--card-radius);
    overflow: hidden;
    box-shadow: 0 18px 40px rgba(0,0,0,.45);
  }

  /* Side 1 – contact */
  .card--contact {
    left: 90px; top: 90px;
    background: linear-gradient(60deg, var(--orange) 0%, var(--red) 30%, var(--magenta) 58%, var(--violet) 78%, var(--cyan) 100%);
    color: var(--white);
  }
  .contact-person {
    position: absolute; left: 44px; top: 40px;
    display: flex; align-items: baseline; gap: 18px;
  }
  .contact-name {
    font-family: "Montserrat", sans-serif; font-weight: 600;
    font-size: 15px; letter-spacing: 6px;
  }
  .contact-title {
    font-family: "Montserrat", sans-serif; font-weight: 500;
    font-size: 9px; letter-spacing: 2.5px;
  }
  .org-mark {
    position: absolute; left: 44px; top: 140px;
    display: flex; align-items: center; gap: 18px;
  }
  .org-dot { width: 62px; height: 62px; border-radius: 50%; background: var(--white); }
  .org-name {
    font-family: "Montserrat", sans-serif; font-weight: 600;
    font-size: 30px; letter-spacing: 4px; line-height: 1.1;
  }
  .contact-row {
    position: absolute; bottom: 34px;
    display: flex; align-items: center; gap: 10px;
    font-size: 15px; letter-spacing: 2px;
  }
  .contact-row--email { left: 44px; }
  .contact-row--phone { right: 40px; }
  .contact-icon {
    width: 24px; height: 24px; border-radius: 50%; background: var(--white);
    display: flex; align-items: center; justify-content: center; flex: none;
  }

  /* Side 2 – product */
  .card--product {
    left: 510px; top: 467px;
    background: var(--white);
    color: var(--ink);
  }
  .product-wave { position: absolute; left: 0; top: 0; width: 600px; height: 120px; }
  .product-mark {
    position: absolute; left: 0; right: 0; top: 112px;
    display: flex; align-items: center; justify-content: center; gap: 14px;
  }
  .product-dot { width: 46px; height: 46px; border-radius: 50%; background: var(--brand-blue); }
  .product-name {
    font-family: "Montserrat", sans-serif; font-weight: 600;
    font-size: 38px; color: var(--brand-blue);
  }
  .product-tagline {
    position: absolute; left: 0; right: 0; top: 190px;
    text-align: center;
    font-family: "Montserrat", sans-serif; font-weight: 500;
    font-size: 14px; letter-spacing: 6px; line-height: 1.45;
    color: var(--ink-soft);
  }
  .product-rule {
    position: absolute; left: 108px; right: 108px; top: 252px; height: 2px;
    background: linear-gradient(90deg, var(--cyan), var(--brand-blue), var(--magenta));
  }
  .product-web {
    position: absolute; left: 108px; top: 266px;
    display: flex; align-items: center; gap: 22px;
    font-size: 17px; letter-spacing: 5px; color: var(--ink-soft);
  }
  .web-icon {
    width: 26px; height: 26px; border-radius: 50%; background: var(--ink-soft);
    display: flex; align-items: center; justify-content: center;
  }
</style>
</head>
<body>

<section class="card card--contact" aria-label="Contact side">
  <div class="contact-person">
    <span class="contact-name">PERRY DUNMORE</span>
    <span class="contact-title">FOUNDER &amp; CEO</span>
  </div>

  <div class="org-mark">
    <span class="org-dot"></span>
    <span class="org-name">BRIGHTLOOM<br>LANGUAGE</span>
  </div>

  <div class="contact-row contact-row--email">
    <span class="contact-icon">
      <svg width="14" height="10" viewBox="0 0 14 10"><rect x="0.5" y="0.5" width="13" height="9" fill="none" stroke="#a12f97" stroke-width="1.2"/><path d="M0.5 0.5 L7 6 L13.5 0.5" fill="none" stroke="#a12f97" stroke-width="1.2"/></svg>
    </span>
    <span>pdunmore@quillpost-mail.net</span>
  </div>

  <div class="contact-row contact-row--phone">
    <span class="contact-icon">
      <svg width="12" height="12" viewBox="0 0 24 24"><path fill="#7a5cc0" d="M6.6 10.8a15.1 15.1 0 0 0 6.6 6.6l2.2-2.2c.3-.3.7-.4 1-.2 1.1.4 2.3.6 3.6.6.6 0 1 .4 1 1V20c0 .6-.4 1-1 1A17 17 0 0 1 3 4c0-.6.4-1 1-1h3.5c.6 0 1 .4 1 1 0 1.3.2 2.5.6 3.6.1.3 0 .7-.2 1z"/></svg>
    </span>
    <span>(555)-014-2286</span>
  </div>
</section>

<section class="card card--product" aria-label="Product side">
  <svg class="product-wave" viewBox="0 0 600 120" preserveAspectRatio="none" aria-hidden="true">
    <defs>
      <linearGradient id="waveGradient" x1="0" y1="0" x2="1" y2="0">
        <stop offset="0" stop-color="#f9a11b"/>
        <stop offset="0.3" stop-color="#ee2a50"/>
        <stop offset="0.6" stop-color="#a12f97"/>
        <stop offset="0.82" stop-color="#7a5cc0"/>
        <stop offset="1" stop-color="#43cbdc"/>
      </linearGradient>
    </defs>
    <path d="M0 0 H600 V100 C520 40 430 10 330 30 C230 50 120 90 0 80 Z" fill="url(#waveGradient)"/>
  </svg>

  <div class="product-mark">
    <span class="product-dot"></span>
    <span class="product-name">Glimworld</span>
  </div>

  <p class="product-tagline">CULTURALLY IMMERSIVE<br>LANGUAGE LEARNING GAMES</p>
  <div class="product-rule"></div>

  <div class="product-web">
    <span class="web-icon">
      <svg width="16" height="16" viewBox="0 0 16 16" fill="none" stroke="#fff" stroke-width="1"><circle cx="8" cy="8" r="6.5"/><ellipse cx="8" cy="8" rx="3" ry="6.5"/><path d="M1.5 8h13M2.5 4.5h11M2.5 11.5h11"/></svg>
    </span>
    <span>www.glimworld-play.com</span>
  </div>
</section>

</body>
</html>
```